Create a memorable Web Design for real estate branding

we are a Minnepolis brokerage and boutique housing specialist with over 27 years of experience in the Global furnished housing industry, servicing the Greater Los Angeles area. Specializing in “warm environments” we offer a customized approach to satisfying our guests and client’s needs by offering a wide array of options in highly desirable areas. Additionally, Lantern Dwelling Partners offers assistance and expertise to home buyers, sellers and investors.

Industry/Entity Type

Real Estate

Number of Pages Required

1 page

Font styles to use
Serif
Sans Serif
Decorative

```html
<!DOCTYPE html>
<html lang="en">
<head>
<meta charset="utf-8">
<title>Lantern Dwelling Partners — Real Estate</title>
<link rel="stylesheet" href="https://fonts.googleapis.com/css2?family=Open+Sans:wght@300;400;600;700&display=swap">
<style>
:root{
  --teal:#1fae8c;
  --green:#7cc242;
  --green-dark:#5aa32a;
  --ink:#444;
  --muted:#8a8a8a;
  --light:#f0f0f0;
  --white:#fff;
}
*{box-sizing:border-box;margin:0;padding:0}
html,body{width:1200px;height:2968px;overflow:hidden}
body{font-family:"Open Sans",Arial,sans-serif;color:var(--ink);background:var(--white);position:relative}
.site-header{position:absolute;top:0;left:0;width:1200px;height:60px;background:var(--white);z-index:2;display:flex;align-items:center;justify-content:space-between;padding:0 130px 0 165px}
.brand{display:flex;align-items:center;gap:8px}
.brand-mark{width:10px;height:10px;background:var(--green)}
.brand-name{font-family:"Open Sans",Arial,sans-serif;font-weight:600;font-size:16px;color:var(--green);white-space:nowrap}
.main-nav{display:flex;gap:28px}
.main-nav a{font-size:13px;color:var(--muted);text-decoration:none;text-transform:uppercase;padding-bottom:6px}
.main-nav a.active{color:var(--teal);border-bottom:2px solid var(--teal)}
.hero{position:absolute;top:0;left:0;width:1200px;height:580px;background:linear-gradient(180deg,#7b9ab8 0%,#a8a193 45%,#6f6a55 75%,#4d5a3a 100%)}
.hero-text{position:absolute;left:165px;top:272px;color:var(--white)}
.hero-text .kicker{font-size:30px;font-weight:300;letter-spacing:1px}
.hero-text h1{font-size:58px;font-weight:600;letter-spacing:1px;line-height:1.1}
.about{position:absolute;top:580px;left:0;width:1200px;height:350px;background:var(--teal);color:var(--white);text-align:center;padding-top:48px}
.section-title{display:flex;align-items:center;justify-content:center;gap:12px;font-size:34px;font-weight:600;letter-spacing:1px}
.about p{width:900px;margin:28px auto 0;font-size:13px;line-height:1.75;text-align:left}
.btn-outline{display:inline-block;margin-top:50px;border:1px solid var(--white);color:var(--white);font-size:13px;padding:7px 22px}
.specialist{position:absolute;top:930px;left:0;width:1200px;height:470px;background:var(--white)}
.specialist-text{position:absolute;left:232px;top:100px;width:300px}
.specialist h2{font-size:34px;font-weight:700;color:var(--teal);line-height:1.1;border-left:6px solid var(--green);padding-left:12px}
.specialist p{font-size:14px;color:var(--teal);line-height:1.6;margin-top:22px}
.specialist p + p{margin-top:18px}
.specialist-visual{position:absolute;left:655px;top:110px;width:290px;height:250px;border-radius:6px;background:radial-gradient(ellipse at 50% 80%,#c9a95d 0%,#d9c28a 30%,#bdd98f 55%,#fff 78%)}
.services-banner{position:absolute;top:1400px;left:0;width:1200px;height:465px;background:linear-gradient(135deg,#3d4a4f 0%,#7b8a8c 40%,#a7b2ad 60%,#4f5d52 100%)}
.services-banner h2{position:absolute;left:232px;top:150px;color:var(--white);font-size:48px;font-weight:600;line-height:1.1;letter-spacing:1px}
.services{position:absolute;top:1865px;left:0;width:1200px;height:495px;display:flex}
.service{width:400px;padding:40px 60px 0;text-align:center}
.service.alt{background:var(--light)}
.service .icon{width:58px;height:58px;margin:0 auto}
.service h3{font-size:26px;font-weight:700;color:var(--teal);line-height:1.05;margin-top:12px;text-transform:uppercase}
.service ul{list-style:none;text-align:left;margin:34px 0 0 30px}
.service li{font-size:11px;color:var(--muted);line-height:1.55;margin-bottom:18px;padding-left:18px;position:relative}
.service li::before{content:"";position:absolute;left:0;top:6px;width:6px;height:6px;border-radius:50%;background:var(--green)}
.contact{position:absolute;top:2360px;left:0;width:1200px;height:520px;background:linear-gradient(160deg,#1d1d1d 0%,#3b3a36 45%,#6d6a62 75%,#2a2926 100%)}
.contact .section-title{color:var(--white);padding-top:72px}
.contact-form{position:absolute;left:370px;top:148px;width:470px}
.row{display:flex;gap:16px;margin-bottom:14px}
.field{flex:1;height:38px;background:var(--white);font:13px "Open Sans",Arial,sans-serif;color:var(--muted);padding:0 10px;display:flex;align-items:center}
.field.area{height:122px;align-items:flex-start;padding-top:10px}
.btn-send{position:absolute;right:0;top:268px;width:145px;height:38px;background:var(--green);color:var(--white);font-size:13px;display:flex;align-items:center;justify-content:center}
.site-footer{position:absolute;top:2880px;left:0;width:1200px;height:88px;background:var(--white);display:flex;align-items:center;justify-content:space-between;padding:0 130px 0 165px}
.site-footer small{font-size:13px;color:var(--green-dark)}
</style>
</head>
<body>
<header class="site-header">
  <div class="brand"><span class="brand-mark"></span><span class="brand-name">Ashby Lane Real Estate</span></div>
  <nav class="main-nav">
    <a class="active" href="#">Home</a><a href="#">Buy</a><a href="#">Sell</a><a href="#">Invest</a><a href="#">Services</a><a href="#">About</a><a href="#">Contacts</a>
  </nav>
</header>

<section class="hero" role="img" aria-label="Photo of a row of townhouses under a blue sky">
  <div class="hero-text">
    <div class="kicker">SPECIALIZING IN</div>
    <h1>WARM ENVIRONMENTS</h1>
  </div>
</section>

<section class="about">
  <div class="section-title">
    <svg width="34" height="26" viewBox="0 0 34 26" fill="#f5d64a"><circle cx="17" cy="7" r="5"/><path d="M8 26c0-7 4-11 9-11s9 4 9 11z"/><circle cx="6" cy="10" r="3.5"/><path d="M0 24c0-5 2.5-8 6-8s4 2 4 2l-3 6z"/><circle cx="28" cy="10" r="3.5"/><path d="M34 24c0-5-2.5-8-6-8s-4 2-4 2l3 6z"/></svg>
    <span>ABOUT US</span>
  </div>
  <p>Lantern Dwelling Partners has welcomed guests and clients for decades, pairing furnished homes with the care of a small local team. We listen first, then match every stay to the neighborhood, budget and rhythm of life each family needs. Our agents know the streets, schools and quiet corners of every area we serve, and we stay close long after the keys change hands. From a short corporate stay to a first home purchase, we keep each step simple, honest and warm, so that moving feels less like a task and more like arriving.</p>
  <span class="btn-outline">MORE</span>
</section>

<section class="specialist">
  <div class="specialist-text">
    <h2>WE ARE<br>SPECIALIST IN</h2>
    <p>Landscape and boutique housing specialist with over 27 years of experience in the Global furnished housing industry, servicing the Greater Los Angeles area.</p>
    <p>*Additionally, Lantern Dwelling Partners offers assistance and expertise to home buyers, sellers and investors.</p>
  </div>
  <div class="specialist-visual" role="img" aria-label="Illustration of a green sprout growing from a pile of coins"></div>
</section>

<section class="services-banner" role="img" aria-label="Photo of a modern glass office building with trees">
  <h2>PERNERING<br>WITH OUR SERVICES</h2>
</section>

<section class="services">
  <div class="service">
    <svg class="icon" viewBox="0 0 58 58"><circle cx="29" cy="29" r="28" fill="none" stroke="#7cc242" stroke-width="2"/><circle cx="29" cy="29" r="21" fill="#7cc242"/><path d="M19 25h20l-3 11H22z M23 25l4-6 M35 25l-4-6" fill="#fff" stroke="#fff" stroke-width="2" stroke-linejoin="round"/></svg>
    <h3>Buy<br>Property</h3>
    <ul>
      <li>We guide buyers to homes that suit their plans and budget.</li>
      <li>Local agents share honest insight on every neighborhood.</li>
      <li>Private tours are arranged at times that work for you.</li>
      <li>Clear offers and fair terms keep each deal moving.</li>
      <li>We stay with you from first visit to final keys.</li>
    </ul>
  </div>
  <div class="service alt">
    <svg class="icon" viewBox="0 0 58 58"><circle cx="29" cy="29" r="28" fill="none" stroke="#7cc242" stroke-width="2"/><circle cx="29" cy="29" r="21" fill="#7cc242"/><path d="M20 30l9-9h8v8l-9 9z" fill="#fff"/><circle cx="33" cy="25" r="1.8" fill="#7cc242"/></svg>
    <h3>Sell<br>Property</h3>
    <ul>
      <li>Accurate pricing built on recent sales near your home.</li>
      <li>Staging advice that helps each room feel welcoming.</li>
      <li>Wide listing reach to bring serious buyers quickly.</li>
      <li>Careful negotiation to protect your final return.</li>
      <li>Simple updates so you always know where things stand.</li>
    </ul>
  </div>
  <div class="service">
    <svg class="icon" viewBox="0 0 58 58"><circle cx="29" cy="29" r="28" fill="none" stroke="#7cc242" stroke-width="2"/><circle cx="29" cy="29" r="21" fill="#7cc242"/><path d="M24 21h10l-3 4c5 2 8 7 8 11H19c0-4 3-9 8-11z" fill="#fff"/><text x="29" y="36" font-family="Open Sans,sans-serif" font-size="10" font-weight="700" fill="#7cc242" text-anchor="middle">$</text></svg>
    <h3>Invest<br>On Property</h3>
    <ul>
      <li>Find rental homes with steady demand and good yields.</li>
      <li>Market reports that show where value is growing.</li>
      <li>Furnished stay options to lift income year round.</li>
      <li>Trusted partners for upkeep, tenants and repairs.</li>
      <li>Long term plans shaped around your own goals.</li>
    </ul>
  </div>
</section>

<section class="contact" role="img" aria-label="Photo of a modern living room interior in dark tones">
  <div class="section-title">
    <svg width="30" height="22" viewBox="0 0 30 22" fill="#7cc242"><path d="M2 14c0-6 6-11 14-11 3 0 6 1 8 2l-4 3c-2-1-3-1-4-1-5 0-9 3-9 7z"/><path d="M8 16c2 3 6 5 10 5 6 0 11-4 11-10l-4 1c0 4-3 6-7 6-2 0-4-1-5-2z"/></svg>
    <span>CONTACT US</span>
  </div>
  <div class="contact-form">
    <div class="row"><div class="field">First Name</div><div class="field">Last Name</div></div>
    <div class="row"><div class="field">Email</div><div class="field">Phone Number</div></div>
    <div class="row"><div class="field area">Your Message</div></div>
    <div class="btn-send">SEND</div>
  </div>
</section>

<footer class="site-footer">
  <div class="brand"><span class="brand-mark"></span><span class="brand-name">Ashby Lane Real Estate</span></div>
  <small>Copyright © 2016, All Rights Reserved</small>
</footer>
</body>
</html>
```